BRIGHT RIVER POWER.

I'd like my business logo.
contact name: Dennis Halvorsen
phone:0438759164
email: info@brightriverpower.net.au
website: www.brightriverpower.net.au

services:
solar
battery storage
LED lighting
energy saving solutions
general electrical
I'd like the design to look professional

Target Market(s)

Everyone

Industry/Entity Type

Business

Contact Information for Business Card

as described above

Requirements
Must have
• Id like the colours and the design to work well with my logo.

```html
<!DOCTYPE html>
<html lang="en">
<head>
<meta charset="utf-8">
<title>Bright River Power – Business Card</title>
<link href="https://fonts.googleapis.com/css2?family=Open+Sans:ital,wght@0,400;0,600;0,700;1,400&display=swap" rel="stylesheet">
<style>
  :root {
    --page-bg: #e9e7e3;
    --card-bg: #f7f7f5;
    --card-edge: #d9d9d4;
    --brand-green: #3f8a1e;
    --deep-green: #2c6d14;
    --band-start: #2f7413;
    --band-end: #5aa52a;
    --band-text: #e4f3c9;
    --band-dot: #9fd36b;
    --ink: #4a4a4a;
    --accent-orange: #e98a1c;
  }
  * { margin: 0; padding: 0; box-sizing: border-box; }
  html, body {
    width: 1200px;
    height: 969px;
    overflow: hidden;
    background: var(--page-bg);
    font-family: "Open Sans", Arial, sans-serif;
  }
  .canvas {
    position: relative;
    width: 1200px;
    height: 969px;
  }
  .business-card {
    position: absolute;
    left: 100px;
    top: 200px;
    width: 1000px;
    height: 569px;
    background: var(--card-bg);
    border: 1px solid var(--card-edge);
    border-radius: 30px;
    box-shadow: 0 18px 40px rgba(0,0,0,0.12);
    overflow: hidden;
  }
  .brand {
    position: absolute;
    left: 56px;
    top: 78px;
    display: flex;
    align-items: center;
    gap: 22px;
  }
  .brand-mark {
    width: 64px;
    height: 64px;
    border-radius: 50%;
    background: var(--accent-orange);
  }
  .brand-name {
    font-weight: 700;
    font-size: 52px;
    letter-spacing: 1px;
    color: var(--brand-green);
    line-height: 1;
  }
  .contact-list {
    position: absolute;
    left: 70px;
    top: 332px;
    list-style: none;
  }
  .contact-item {
    display: flex;
    align-items: center;
    gap: 14px;
    font-size: 26px;
    color: var(--ink);
    height: 39px;
  }
  .contact-icon {
    width: 22px;
    height: 22px;
    flex: none;
  }
  .contact-name {
    position: absolute;
    left: 688px;
    top: 362px;
    font-weight: 700;
    font-size: 34px;
    color: var(--deep-green);
  }
  .services-band {
    position: absolute;
    left: 0;
    top: 494px;
    width: 100%;
    height: 45px;
    background: linear-gradient(90deg, var(--band-start), var(--band-end));
    display: flex;
    align-items: center;
    padding-left: 122px;
    gap: 12px;
    font-style: italic;
    font-size: 24px;
    color: var(--band-text);
  }
  .service-dot {
    width: 9px;
    height: 9px;
    border-radius: 50%;
    background: var(--band-dot);
  }
</style>
</head>
<body>
<main class="canvas">
  <article class="business-card">
    <header class="brand">
      <span class="brand-mark"></span>
      <span class="brand-name">BRIGHT RIVER POWER</span>
    </header>

    <ul class="contact-list">
      <li class="contact-item">
        <svg class="contact-icon" viewBox="0 0 24 24" aria-hidden="true">
          <path fill="#3f8a1e" d="M6.6 10.8c1.4 2.8 3.8 5.1 6.6 6.6l2.2-2.2c.3-.3.7-.4 1-.2 1.1.4 2.3.6 3.6.6.6 0 1 .4 1 1V20c0 .6-.4 1-1 1C10.6 21 3 13.4 3 4c0-.6.4-1 1-1h3.5c.6 0 1 .4 1 1 0 1.2.2 2.4.6 3.6.1.3 0 .7-.2 1z"/>
        </svg>
        <span>0438759164</span>
      </li>
      <li class="contact-item">
        <svg class="contact-icon" viewBox="0 0 24 24" aria-hidden="true">
          <rect x="2" y="5" width="20" height="14" rx="1.5" fill="#3f8a1e"/>
          <path d="M3 6.5l9 6.5 9-6.5" fill="none" stroke="#f7f7f5" stroke-width="1.6"/>
        </svg>
        <span>info@brightriverpower.net.au</span>
      </li>
      <li class="contact-item">
        <svg class="contact-icon" viewBox="0 0 24 24" aria-hidden="true">
          <circle cx="12" cy="12" r="10" fill="#3f8a1e"/>
          <path d="M2 12h20M12 2c3 3 3 17 0 20M12 2c-3 3-3 17 0 20" fill="none" stroke="#f7f7f5" stroke-width="1.4"/>
        </svg>
        <span>www.brightriverpower.net.au</span>
      </li>
    </ul>

    <p class="contact-name">Dennis Halvorsen</p>

    <footer class="services-band">
      <span>solar</span><span class="service-dot"></span>
      <span>battery storage</span><span class="service-dot"></span>
      <span>LED lighting</span><span class="service-dot"></span>
      <span>energy saving solutions</span>
    </footer>
  </article>
</main>
</body>
</html>
```